Single-sided business card for restaurant velmora with new logo made on this site

Business card options with new logo including restaurant name, address, phone number and website. This business card is single-sided only and will be presented at the hostess desk for clients to take. I would like to see options based on a cream card background, a white card background, a yellow card background and a burgundy colored background. It needs to be elegant and traditional.

Target Market(s)

local and international crowd

Industry/Entity Type

restaurant

Contact Information for Business Card

address, website and phone number

Font styles to use
Serif

Colors
EE7325
F08F49
F5BC92
FAE3D3
FDF4ED

Requirements
Must have
• new logo, address, phone number, website
Should not have
• more than three colors

```html
<!DOCTYPE html>
<html lang="es">
<head>
<meta charset="utf-8">
<title>Velmora – Tarjeta de presentación</title>
<link href="https://fonts.googleapis.com/css2?family=Cinzel:wght@500&family=EB+Garamond:wght@500&family=Arimo:wght@400&display=swap" rel="stylesheet">
<style>
  :root {
    --stage: #1c1c1c;
    --card: #ffffff;
    --gold: #f4b02a;
    --brown: #3d1414;
    --rule: #c9c9c9;
  }
  * { margin: 0; padding: 0; box-sizing: border-box; }
  html, body { width: 1200px; height: 900px; overflow: hidden; }
  body { background: var(--stage); position: relative; }

  .business-card {
    position: absolute;
    left: 110px; top: 170px;
    width: 980px; height: 560px;
    background: var(--card);
    border: 9px solid var(--gold);
  }

  .brand {
    position: absolute;
    left: 150px; top: 120px;
    width: 250px; height: 320px;
    display: flex; flex-direction: column; align-items: center; justify-content: center;
    gap: 26px;
  }
  .brand-square {
    width: 150px; height: 150px;
    background: var(--gold);
  }
  .brand-name {
    font-family: "Cinzel", serif;
    font-weight: 500;
    font-size: 40px;
    letter-spacing: 8px;
    color: var(--brown);
  }

  .divider {
    position: absolute;
    left: 470px; top: 170px;
    width: 1.5px; height: 250px;
    background: var(--rule);
  }

  .contact {
    position: absolute;
    left: 530px; top: 168px;
    color: var(--brown);
  }
  .reservations-label {
    font-family: "Cinzel", serif;
    font-weight: 500;
    font-size: 27px;
    letter-spacing: 2px;
    color: var(--gold);
  }
  .phone {
    font-family: "EB Garamond", serif;
    font-weight: 500;
    font-size: 44px;
    line-height: 1;
    margin-top: 2px;
  }
  .website {
    font-family: "Arimo", sans-serif;
    font-size: 22px;
    margin-top: 30px;
  }
  .address {
    font-family: "Arimo", sans-serif;
    font-size: 22px;
    line-height: 1.3;
    font-style: normal;
    margin-top: 30px;
  }
</style>
</head>
<body>
  <section class="business-card">
    <div class="brand">
      <div class="brand-square"></div>
      <div class="brand-name">VELMORA</div>
    </div>

    <div class="divider"></div>

    <div class="contact">
      <div class="reservations-label">RESERVACIONES</div>
      <div class="phone">958-412-3076</div>
      <div class="website">www.velmora.com.mx</div>
      <address class="address">
        Restaurant Velmora<br>
        Almendro 318<br>
        Bahías de Santa Lucía<br>
        Oaxaca CP 70431
      </address>
    </div>
  </section>
</body>
</html>
```